Tax Preparation flyer for LedgerVale Corp.

My Client would like a one page PDF flyer to promote upcoming tax season in Canada. This firm is affordable and all virtual. I have attached a copy of their logo and a word document with the proposed wording for the flyer. Please feel free to change if you have better suggestions.

Target Market(s)

individuals in canada

Colors
0054AA
0677BA
7BADD7
CADEEF
E8F1F8

```html
<!DOCTYPE html>
<html lang="en">
<head>
<meta charset="utf-8">
<title>LedgerVale Corp. – Tax Season Flyer</title>
<link href="https://fonts.googleapis.com/css2?family=Poppins:wght@400;500;600;700&display=swap" rel="stylesheet">
<style>
  :root{
    --blue:#1b9ad7;
    --charcoal:#36383b;
    --slate:#41637a;
    --ink:#2f3033;
    --text:#3b3c3f;
    --white:#ffffff;
    --stage:#e4e5e6;
    --photo-a:#dfe6ec;
    --photo-b:#c7d3dc;
  }
  *{box-sizing:border-box;margin:0;padding:0}
  html,body{width:1200px;height:1200px;overflow:hidden;background:var(--stage)}
  body{font-family:"Poppins",sans-serif;color:var(--text)}
  .flyer{position:absolute;left:172px;top:0;width:856px;height:1200px;background:var(--white);overflow:hidden}
  .hero-shapes{position:absolute;left:0;top:0}
  .photo{position:absolute;left:190px;top:233px;width:666px;height:374px;
    background:linear-gradient(120deg,var(--photo-a) 0%,#eef2f5 45%,var(--photo-b) 100%)}
  .headline{position:absolute;right:30px;top:8px;text-align:right}
  .headline-main{font-size:100px;font-weight:700;color:var(--blue);line-height:1;letter-spacing:-1px}
  .headline-sub{font-size:33px;font-weight:500;color:var(--ink);line-height:1.1;margin-top:2px}
  .intro{position:absolute;right:30px;top:146px;text-align:right;font-size:13.5px;line-height:19.6px;color:var(--text);white-space:nowrap}
  .intro strong,.meet strong{color:var(--blue);font-weight:600}
  .photo-band{position:absolute;left:0;top:607px;width:856px;height:10px;background:var(--charcoal)}
  .photo-band::before{content:"";position:absolute;left:0;top:0;width:671px;height:10px;background:var(--blue)}
  .meet{position:absolute;left:30px;top:622px;width:764px;font-size:15.6px;line-height:22px;color:var(--text)}
  .meet-line{display:block;white-space:nowrap}
  .meet-line--full{text-align:justify;text-align-last:justify}
  .pricing{position:absolute;left:29px;top:677px;width:797px;height:340px;background:var(--charcoal);border-radius:10px}
  .pricing-tab{position:absolute;left:264px;top:-12px;width:276px;height:44px}
  .pricing-title{position:absolute;left:0;right:0;top:-12px;text-align:center;font-size:32px;font-weight:700;color:var(--white);line-height:44px}
  .plan{position:absolute;top:41px;width:246px;height:290px}
  .plan--basic{left:10px}
  .plan--premium{left:274px}
  .plan--business{left:541px}
  .divider{position:absolute;top:42px;width:2px;height:274px;background:var(--blue)}
  .divider--one{left:264px}.divider--two{left:530px}
  .plan-head{height:34px;background:var(--white);border-radius:4px;display:flex;align-items:center;justify-content:space-between;padding:0 6px 0 8px}
  .plan-name{font-size:23.5px;font-weight:700;color:var(--ink);line-height:1}
  .plan-price{background:var(--blue);color:var(--white);font-size:23px;font-weight:500;border-radius:14px;padding:0 9px;line-height:26px}
  .plan-unit{font-size:13px;line-height:15px;text-align:center;color:var(--ink)}
  .features{list-style:none;margin-top:6.5px}
  .features li{position:relative;padding-left:15px;font-size:12.5px;line-height:17px;color:var(--white);margin-bottom:6px;white-space:nowrap}
  .features li::before{content:"";position:absolute;left:0;top:3.5px;width:10px;height:10px;border-radius:50%;background:var(--blue)}
  .features li::after{content:"";position:absolute;left:3.3px;top:5.7px;width:2.6px;height:4.4px;border:solid var(--white);border-width:0 1.4px 1.4px 0;transform:rotate(40deg)}
  .plan-rule{position:absolute;left:77px;top:225px;width:92px;height:2px;background:var(--blue)}
  .plan-note{position:absolute;left:0;top:231px;font-size:12.2px;line-height:17px;color:var(--white);padding-left:15px;white-space:nowrap}
  .catchup{position:absolute;left:0;width:856px;top:1020px;text-align:center;font-size:20.5px;font-weight:600;color:var(--ink)}
  .catchup span{color:var(--blue)}
  .catchup-box{position:absolute;left:88px;top:1052px;width:678px;height:29px;border:1.5px solid var(--ink);border-radius:5px;box-shadow:2px 2px 0 var(--ink);text-align:center;font-size:13.8px;line-height:26px;color:var(--text)}
  .catchup-box strong{color:var(--blue);font-weight:600}
  .contact-shapes{position:absolute;left:0;top:1114px}
  .contact-title{position:absolute;left:30px;top:1115px;font-size:24.5px;font-weight:700;color:var(--white);line-height:32px}
  .contact-item{position:absolute;top:1159px;display:flex;align-items:center;gap:7px;font-size:14.5px;color:var(--white)}
  .contact-item--email{left:30px}.contact-item--phone{left:219px}
  .brand{position:absolute;right:30px;top:1124px;text-align:right;color:var(--ink);font-weight:700;line-height:1}
  .brand-name{font-size:34px;letter-spacing:-0.5px}
  .brand-sub{font-size:22px;margin-top:4px}
</style>
</head>
<body>
<main class="flyer">
  <div class="photo" role="img" aria-label="Photo of a relaxed businessman meditating at his desk by a bright office window"></div>

  <svg class="hero-shapes" width="856" height="620" viewBox="0 0 856 620" aria-hidden="true">
    <polygon points="0,0 80,0 241,233 190,233 82,49 0,49" fill="var(--blue)"/>
    <polygon points="0,49 82,49 190,233 87,607 0,607" fill="var(--slate)"/>
    <polygon points="190,233 87,607 472,607" fill="rgba(88,90,94,0.62)"/>
  </svg>

  <header class="headline">
    <h1 class="headline-main">Relax!</h1>
    <p class="headline-sub">We’ve Got Your Taxes Covered!</p>
  </header>

  <p class="intro">It has never been easier to file your taxes.&nbsp; Our virtual tax office let’s you file from the<br>comfort of your home or office and know that our tax expects have taken care of all<br>the work. Completely virtual, forms are signed via <strong>SignFlow</strong> and you can upload<br>documents to us and receive documents from us in our <strong>Secured Client Portal</strong>.</p>

  <div class="photo-band"></div>

  <p class="meet"><span class="meet-line meet-line--full">Need a tax review or have questions, our tax experts are available on <strong>MeetHub, TalkRoom or</strong></span><span class="meet-line"><strong>CallSpace</strong> for your convenience.</span></p>

  <section class="pricing">
    <svg class="pricing-tab" width="276" height="44" viewBox="0 0 276 44" aria-hidden="true">
      <path d="M0,0 H276 C262,0 258,8 250,18 C238,36 228,44 200,44 H76 C48,44 38,36 26,18 C18,8 14,0 0,0 Z" fill="var(--blue)"/>
    </svg>
    <h2 class="pricing-title">Pricing</h2>

    <div class="divider divider--one"></div>
    <div class="divider divider--two"></div>

    <article class="plan plan--basic">
      <div class="plan-head"><span class="plan-name">Basic</span><span class="plan-price">$95</span><span class="plan-unit">Per<br>return</span></div>
      <ul class="features">
        <li>Full tax preparation from start to<br>finish by a tax expert</li>
        <li>RRSP, donations &amp; medical expenses</li>
        <li>ideal for newcomers, students &amp;<br>seniors</li>
        <li>Maximum refund guranteed</li>
        <li>Audit representation (valued at $30)</li>
      </ul>
      <div class="plan-rule"></div>
    </article>

    <article class="plan plan--premium">
      <div class="plan-head"><span class="plan-name">Premium</span><span class="plan-price">$125</span><span class="plan-unit">Per<br>return</span></div>
      <ul class="features">
        <li>Full tax preparation from start to<br>finish by a tax expert</li>
        <li>Emigrant tax return</li>
        <li>Final (deceased) tax return</li>
        <li>Claim industry specific deductions<br>to lower tax owing</li>
        <li>Audit representation (valued at $30)</li>
      </ul>
      <div class="plan-rule"></div>
    </article>

    <article class="plan plan--business">
      <div class="plan-head"><span class="plan-name">Business</span><span class="plan-price">$195</span><span class="plan-unit">Per<br>return</span></div>
      <ul class="features">
        <li>Full tax preparation from start to<br>finish by a tax expert</li>
        <li>Business/self-employment income</li>
        <li>Rental property*</li>
        <li>Partnership income</li>
        <li>Non-resident tax return</li>
        <li>Trust action(T3)</li>
        <li>Audit representation (valued at $50)</li>
      </ul>
      <div class="plan-rule"></div>
      <p class="plan-note">* Fee included one rental property, or<br>one business</p>
    </article>
  </section>

  <h3 class="catchup">Have you fallen behind <span>in your taxes</span>?</h3>
  <p class="catchup-box">File 3 or more years and receive a <strong>20% discount</strong>.&nbsp; We can file back to <strong>2012</strong>.</p>

  <svg class="contact-shapes" width="856" height="86" viewBox="0 0 856 86" aria-hidden="true">
    <polygon points="0,0 170,0 202,33 0,33" fill="var(--blue)"/>
    <polygon points="0,33 372,33 425,86 0,86" fill="var(--charcoal)"/>
    <polygon points="372,33 384,33 437,86 425,86" fill="var(--blue)"/>
  </svg>
  <h2 class="contact-title">Contact us:</h2>
  <div class="contact-item contact-item--email">
    <svg width="20" height="20" viewBox="0 0 20 20" aria-hidden="true"><circle cx="10" cy="10" r="9" fill="none" stroke="#fff" stroke-width="1.2"/><rect x="5.5" y="7" width="9" height="6.5" fill="none" stroke="#fff" stroke-width="1"/><path d="M5.5 7 L10 10.6 L14.5 7" fill="none" stroke="#fff" stroke-width="1"/></svg>
    <span>hello@ledgervale.ca</span>
  </div>
  <div class="contact-item contact-item--phone">
    <svg width="20" height="20" viewBox="0 0 20 20" aria-hidden="true"><circle cx="10" cy="10" r="9" fill="none" stroke="#fff" stroke-width="1.2"/><path d="M7.2 5.6 L8.6 5.4 L9.3 8 L8.3 8.8 C8.9 10.2 9.8 11.1 11.2 11.7 L12 10.7 L14.6 11.4 L14.4 12.8 C14.2 13.6 13.4 14 12.6 13.9 C9.2 13.4 6.6 10.8 6.1 7.4 C6 6.6 6.4 5.8 7.2 5.6 Z" fill="none" stroke="#fff" stroke-width="1"/></svg>
    <span>(877) 555-0142</span>
  </div>

  <div class="brand">
    <div class="brand-name">LedgerVale</div>
    <div class="brand-sub">Corp.</div>
  </div>
</main>
</body>
</html>
```